Electrical Contracting business card design

We need a simple business card design for an Electrical Contracting business. A simple design would be appreciated
This company has 2 directors so on one it would have Glen Moraty & another with Dana Moraty.
Updates

Project Deadline Extended
Reason: Hello A few designers have asked for a logo unfortunately we don't have one so have extended deadline to see who can help us out with this. CHEERS

Project Deadline Extended
Reason: Waiting for business partner to return from xmas break. cheers

Industry/Entity Type

Business

Contact Information for Business Card

Volquin Electrical Services P/L
REC: 47302
Residential Commercial Industrial
Service-Repairs-Renovations-Installations-Telephone-Data
Glen Moraty-Ph: 0438 615 207
Email: glen@volquinelectrical.com.au

Requirements
Should not have
• The design should not have any electrical appliances in it ie: power-points, leads, houses etc.

```html
<!DOCTYPE html>
<html lang="en">
<head>
<meta charset="utf-8">
<title>Volquin Electrical Services – Business Card</title>
<link rel="stylesheet" href="https://fonts.googleapis.com/css2?family=Bebas+Neue&family=Josefin+Sans:wght@300;400&display=swap">
<style>
  :root {
    --page: #ffffff;
    --card: #111111;
    --accent: #f5851f;
    --ink-dark: #1c1a1a;
  }
  * { margin: 0; padding: 0; box-sizing: border-box; }
  html, body {
    width: 1200px;
    height: 1000px;
    overflow: hidden;
    background: var(--page);
  }
  .canvas { position: relative; width: 1200px; height: 1000px; }

  .card {
    position: absolute;
    background: var(--card);
    overflow: hidden;
  }
  .card--front { left: 24px; top: 15px; width: 752px; height: 464px; }
  .card--back  { left: 422px; top: 517px; width: 757px; height: 466px; }

  .company-name {
    font-family: "Bebas Neue", "Oswald", sans-serif;
    color: var(--accent);
    letter-spacing: 0.3px;
    white-space: nowrap;
  }
  .card--front .company-name {
    position: absolute;
    left: 0; right: 0;
    top: 225px;
    text-align: center;
    font-size: 33px;
    line-height: 36px;
    padding-left: 8px;
  }

  .director {
    position: absolute;
    top: 107px;
    font-family: "Josefin Sans", sans-serif;
    color: var(--accent);
    font-weight: 400;
    white-space: nowrap;
  }
  .director--left  { right: 517px; text-align: right; }
  .director--right { left: 511px; text-align: left; }

  .director__name  { font-size: 21px; line-height: 24px; font-weight: 300; }
  .director__role  { font-size: 13px; line-height: 14px; }
  .director__phone,
  .director__email,
  .director__licence { font-size: 12px; line-height: 18px; }
  .director__email { font-size: 10px; }
  .director--left .director__phone { padding-right: 3px; }
  .director--left .director__role  { padding-right: 2px; }

  .services { list-style: none; font-size: 10px; line-height: 13.7px; }

  .divider {
    position: absolute;
    left: 372px;
    top: 112px;
    width: 3px;
    height: 182px;
    background: var(--accent);
  }

  .footer-band {
    position: absolute;
    left: 0; right: 0; bottom: 0;
    height: 96px;
    background: var(--accent);
  }
  .footer-band .company-name {
    position: absolute;
    right: 45px;
    top: 33px;
    color: var(--ink-dark);
    font-size: 21px;
    line-height: 24px;
  }
</style>
</head>
<body>
<main class="canvas">

  <section class="card card--front" aria-label="Card front">
    <h1 class="company-name">Volquin Electrical Services</h1>
  </section>

  <section class="card card--back" aria-label="Card back">
    <div class="director director--left">
      <p class="director__name">Glen Moraty</p>
      <p class="director__role">Directors</p>
      <p class="director__phone">0438 615 207</p>
      <p class="director__email">Email: glen@volquinelectrical.com.au</p>
      <p class="director__licence">P/L REC: 47302</p>
      <ul class="services">
        <li>Residential Commercial</li>
        <li>IndustrialService</li>
        <li>Repairs</li>
        <li>Renovations</li>
        <li>Installations</li>
        <li>Telephone</li>
        <li>Data</li>
      </ul>
    </div>

    <div class="divider" aria-hidden="true"></div>

    <div class="director director--right">
      <p class="director__name">Dana Moraty</p>
      <p class="director__role">Directors</p>
      <p class="director__phone">0438 615 207</p>
      <p class="director__email">Email: glen@volquinelectrical.com.au</p>
      <p class="director__licence">P/L REC: 47302</p>
      <ul class="services">
        <li>Residential Commercial</li>
        <li>IndustrialService</li>
        <li>Repairs</li>
        <li>Renovations</li>
        <li>Installations</li>
        <li>Telephone</li>
        <li>Data</li>
      </ul>
    </div>

    <footer class="footer-band">
      <p class="company-name">Volquin Electrical Services</p>
    </footer>
  </section>

</main>
</body>
</html>
```